Broschüre für Personaldienstleister
Zielgruppe
Wir sind ein Personaldienstleister und vermitteln ausländisches medizinisches Fachpersonal an deutsche Einrichtungen. Unsere Zielgruppe sind Krankenhäuser, Pflegeheime, Ärztehäuser, Praxen, Labore und weitere medizinische Institutionen.
Aufgabenstellung
Wir haben eine Infobroschüre sowie eine PowerPoint Präsentation bereits mit einem groben Design erstellt. Texte und Beispielbilder (Stockmaterial) sind ebenfalls vorhanden, gerne wünschen wir uns auch Eigeninitiative bei der Wahl der Bilder passend zum neuen Design.
Wir wünschen uns ein Redesign mit einem kreativen, einzigartigen Design. Zudem ist uns wichtig, dass unsere Infografiken qualitativ und hochwertig gestaltet werden.
Dieses Projekt ist mit zukünftigen Folgeprojekten verbunden, da wir weitere Präsentationen und Broschüren für andere Zielgruppen benötigen.

```html
<!DOCTYPE html>
<html lang="de">
<head>
<meta charset="utf-8">
<title>Veldara HR – Broschüre</title>
<link href="https://fonts.googleapis.com/css2?family=Heebo:wght@400;500;700&family=Roboto+Condensed:wght@500;700&display=swap" rel="stylesheet">
<style>
:root{
  --bg:#858585;
  --paper:#ffffff;
  --ink:#1b3f47;
  --green:#3d8a6f;
  --mint:#c6e4d9;
  --mint-soft:#d3e8e0;
  --panel:#d6d6d4;
  --text:#3a3a3a;
  --muted:#555;
}
*{margin:0;padding:0;box-sizing:border-box}
html,body{width:845px;height:1200px;overflow:hidden;background:var(--bg)}
body{position:relative;font-family:"Heebo",Arial,sans-serif;color:var(--text)}
.page{position:absolute;background:var(--paper);overflow:hidden}
.page svg.art{position:absolute;left:0;top:0}
.footer{position:absolute;height:17px;background:var(--ink);color:#fff;font-size:6.6px;display:flex;align-items:center;justify-content:space-around}
.page-title{position:absolute;color:var(--ink);font-weight:700;line-height:1.15}

/* page 1 */
.p1{left:14px;top:36px;width:405px;height:565px}
.p1 .page-title{left:0;width:405px;text-align:center;top:18px;font-size:21.5px}
.step-no{position:absolute;font-family:"Roboto Condensed",Arial,sans-serif;font-weight:700;color:var(--ink);font-size:15px;line-height:1;transform:translateY(-50%)}
.step-text{position:absolute;font-size:4.4px;line-height:1.28;color:var(--muted);width:92px}
.p1 .footer{left:4px;right:4px;bottom:5px}

/* page 2 */
.p2{left:422px;top:36px;width:412px;height:565px}
.p2 .panel{position:absolute;left:4px;top:4px;right:4px;bottom:4px;background:var(--panel)}
.p2 .page-title{left:39px;top:24px;font-size:21px;width:340px}
.p2 .copy{position:absolute;left:39px;top:81px;width:333px;font-size:8.3px;line-height:1.24;text-align:justify;color:#2b2b2b}
.p2 .copy p{margin-bottom:10px}
.photo-meeting{position:absolute;left:4px;top:324px;right:4px;bottom:4px;background:linear-gradient(160deg,#e4e4e2 0%,#cfcfcc 40%,#3c3f46 70%,#e9e6e0 100%)}

/* page 3 */
.p3{left:13px;top:610px;width:406px;height:572px}
.p3 .page-title{left:0;width:406px;text-align:center;top:34px;font-size:18px}
.tl-text{position:absolute;font-size:5.9px;line-height:1.22;color:var(--muted)}
.tl-text h3{font-size:6px;font-weight:500;color:var(--ink)}
.tl-text.right{text-align:justify}
.first-day{position:absolute;left:16px;top:484px;width:375px}
.first-day h2{font-size:11.5px;font-weight:500;color:var(--ink);line-height:1.1}
.first-day p{font-size:6.4px;line-height:1.26;color:var(--muted)}
.p3 .footer{left:4px;right:4px;bottom:4px}

/* page 4 */
.p4{left:427px;top:610px;width:407px;height:572px}
.photo-team{position:absolute;left:4px;top:5px;width:400px;height:255px;background:linear-gradient(180deg,#f3f5f7 0%,#eef1f4 35%,#7fb3dc 70%,#e8eef3 100%)}
.p4 .page-title{left:0;width:407px;text-align:center;top:275px;font-size:18px}
.talent-list{position:absolute;left:14px;width:380px;top:306px;text-align:center;font-size:9.2px;line-height:1.25;color:#4a4a4a}
.talent-more{position:absolute;left:0;width:407px;top:387px;text-align:center;font-size:9px;color:var(--green)}
.photo-hands{position:absolute;left:119px;top:419px;width:168px;height:106px;border-radius:9px;background:linear-gradient(135deg,#5e5348 0%,#c9bfb3 45%,#efece8 100%)}
.p4 .footer{left:4px;right:4px;bottom:4px}
</style>
</head>
<body>

<!-- Page: Rekrutierungsverfahren -->
<section class="page p1">
  <h1 class="page-title">Unser Rekrutierungsverfahren</h1>
  <svg class="art" width="405" height="565" viewBox="0 0 405 565">
    <defs>
      <g id="ring">
        <circle r="28" fill="var(--mint)"/>
        <circle r="34" fill="none" stroke="var(--ink)" stroke-width="0.8" stroke-dasharray="38 176" transform="rotate(-150)"/>
        <circle r="34" fill="none" stroke="var(--ink)" stroke-width="0.8" stroke-dasharray="34 180" transform="rotate(-20)"/>
        <circle r="34" fill="none" stroke="var(--ink)" stroke-width="0.8" stroke-dasharray="40 174" transform="rotate(85)"/>
      </g>
    </defs>
    <g fill="none" stroke="var(--ink)" stroke-width="0.7" stroke-dasharray="2 1.5">
      <path d="M160 76 H147 V158 H165"/>
      <path d="M39 191 H26 V274 H41"/><path d="M157 191 H144 V274 H159"/><path d="M289 195 H277 V276 H294"/>
      <path d="M39 307 H26 V388 H41"/><path d="M157 307 H144 V388 H159"/><path d="M289 307 H277 V389 H292"/>
      <path d="M39 420 H26 V502 H41"/><path d="M157 420 H144 V502 H159"/><path d="M289 421 H277 V502 H291"/>
    </g>
    <g fill="var(--ink)">
      <circle cx="160" cy="76" r="4.5"/><circle cx="165" cy="158" r="4.5"/>
      <circle cx="39" cy="191" r="4.5"/><circle cx="41" cy="274" r="4.5"/>
      <circle cx="157" cy="191" r="4.5"/><circle cx="159" cy="274" r="4.5"/>
      <circle cx="289" cy="195" r="4.5"/><circle cx="294" cy="276" r="4.5"/>
      <circle cx="39" cy="307" r="4.5"/><circle cx="41" cy="388" r="4.5"/>
      <circle cx="157" cy="307" r="4.5"/><circle cx="159" cy="388" r="4.5"/>
      <circle cx="289" cy="307" r="4.5"/><circle cx="292" cy="389" r="4.5"/>
      <circle cx="39" cy="420" r="4.5"/><circle cx="41" cy="502" r="4.5"/>
      <circle cx="157" cy="420" r="4.5"/><circle cx="159" cy="502" r="4.5"/>
      <circle cx="289" cy="421" r="4.5"/><circle cx="291" cy="502" r="4.5"/>
    </g>
    <use href="#ring" x="200" y="89"/>
    <use href="#ring" x="79" y="204"/><use href="#ring" x="198" y="200"/><use href="#ring" x="329" y="204"/>
    <use href="#ring" x="80" y="314"/><use href="#ring" x="200" y="314"/><use href="#ring" x="327" y="319"/>
    <use href="#ring" x="82" y="432"/><use href="#ring" x="199" y="432"/><use href="#ring" x="327" y="434"/>
    <g fill="none" stroke="var(--ink)" stroke-width="1.6" stroke-linecap="round" stroke-linejoin="round">
      <!-- form -->
      <rect x="187" y="75" width="22" height="28" rx="2"/><path d="M192 83h12M192 89h12M192 95h8M205 101l7-8"/>
      <!-- speech -->
      <path d="M64 197a12 9 0 1 1 6 9l-6 4z"/><path d="M88 206a9 7 0 0 1 5 10l3 4-5-2"/>
      <!-- documents -->
      <rect x="188" y="186" width="16" height="24" rx="1.5"/><rect x="194" y="182" width="16" height="24" rx="1.5"/>
      <!-- hands -->
      <circle cx="324" cy="197" r="3.5"/><circle cx="334" cy="197" r="3.5"/><path d="M316 212c2-6 7-7 12-7s10 1 12 7M312 205v10l8 6M346 205v10l-8 6"/>
      <!-- interview -->
      <path d="M68 322h24M72 322v10M88 322v10"/><circle cx="70" cy="309" r="3"/><circle cx="90" cy="309" r="3"/><rect x="76" y="300" width="9" height="7" rx="1.5"/>
      <!-- stacked docs -->
      <rect x="188" y="304" width="20" height="24"/><rect x="192" y="300" width="20" height="24" fill="var(--mint)"/><path d="M196 307h12M196 312h12M196 317h8"/>
      <!-- house -->
      <path d="M313 322l14-13 14 13M317 319v14h20v-14M324 333v-6h6v6"/>
      <!-- traveler -->
      <circle cx="86" cy="420" r="3"/><path d="M85 424l-4 9 6 5M81 433l-5 7M74 428h6v10h-6zM68 442h28"/>
      <!-- nurse -->
      <circle cx="199" cy="428" r="6"/><path d="M193 421h12M189 447c0-8 4-11 10-11s10 3 10 11z"/>
      <!-- puzzle -->
      <path d="M316 424h9a3 3 0 1 1 5 0h8v9a3 3 0 1 1 0 5v8h-22z"/><path d="M327 424v22M316 435h22"/>
    </g>
  </svg>

  <span class="step-no" style="left:151px;top:135px">01</span>
  <p class="step-text" style="left:170px;top:127px">Bewerber:in wird auf uns Aufmerksam, füllt unser Bewerbungsformular aus und reicht die nötigen Dokumente ein.</p>

  <span class="step-no" style="left:29px;top:249px">02</span>
  <p class="step-text" style="left:49px;top:241px;width:88px">Um das erforderliche Sprachniveau B2 zu erreichen, bieten wir Bewerber:innen kostenlose interne Sprachkurse an.</p>
  <span class="step-no" style="left:147px;top:242px">03</span>
  <p class="step-text" style="left:166px;top:233px">Parallel zu ihren sprachlichen Vorbereitungen beginnen die Bewerber:innen mit dem Anerkennungsprozess.</p>
  <span class="step-no" style="left:280px;top:249px">04</span>
  <p class="step-text" style="left:300px;top:240px">Wir bereiten unsere Kandidat:innen auf die bevorstehenden Videointerviews vor und erarbeiten proaktive Lösungen für Situationen, die während des Vorstellungsgesprächs auftreten können.</p>

  <span class="step-no" style="left:30px;top:364px">05</span>
  <p class="step-text" style="left:52px;top:354px;width:76px">Die Bewerber:innen haben Vorstellungsgespräche mit potenziellen Arbeitgebern aus Deutschland. Wir begleiten Sie dabei.</p>
  <span class="step-no" style="left:148px;top:373px">06</span>
  <p class="step-text" style="left:168px;top:355px">Bei erfolgreicher Einigung kommt es zur Unterzeichnung eines Arbeitsvertrags. Wir kümmern uns um die weiteren Prozessabläufe.</p>
  <span class="step-no" style="left:279px;top:367px">07</span>
  <p class="step-text" style="left:298px;top:357px">Die für die Beschäftigung in Deutschland erforderlichen Dokumente werden von uns erstellt bzw. eingeholt und wir suchen eine Unterkunft in der Nähe des künftigen Arbeitsortes.</p>

  <span class="step-no" style="left:32px;top:480px">08</span>
  <p class="step-text" style="left:52px;top:471px;width:80px">Einreise Ihres/r neune Mitarbeiter:in nach Deutschland. Wir organisieren die Abholung vom Flughafen und den Transport zur Unterkunft.</p>
  <span class="step-no" style="left:149px;top:480px">09</span>
  <p class="step-text" style="left:169px;top:471px">Wir bereiten Ihre neue Fachkraft auf den Arbeitsantritt vor und begleiten sie zum ersten Arbeitstag.</p>
  <span class="step-no" style="left:279px;top:479px">10</span>
  <p class="step-text" style="left:297px;top:471px">Unsere Kandidat:innen werden während der gesamten Probe-/Einarbeitungszeit von uns unterstützt und betreut.</p>

  <footer class="footer"><span>+49 000 555 01 230</span><span>hr@veldara-hr.example</span><span>www.veldara-hr.example</span></footer>
</section>

<!-- Page: Kosten -->
<section class="page p2">
  <div class="panel"></div>
  <h1 class="page-title">Was kostet eine gute und faire Rekrutierung bei uns?</h1>
  <div class="copy">
    <p>Wir bei Veldara HR legen großen Wert auf Kundenzufriedenheit. Mit unserem 360°-Service decken wir alle wichtigen Serviceleistungen rund um die Rekrutierung von ausländischen Fachkräften ab und bieten Ihnen dadurch noch mehr Flexibilität und Dynamik.</p>
    <p>Bei der Berechnung unserer Preise spielen somit viele Faktoren eine wichtige Rolle und sind stark abhängig vom Leistungsumfang und der Art der Rekrutierung.</p>
    <p>Preisangebote kalkulieren wir individuell und Bedarfsgerecht erst mit einer konkreten und detaillierten Nachfrage.</p>
    <p>Teilen Sie uns jetzt Ihren Personalbedarf mit!</p>
  </div>
  <div class="photo-meeting" role="img" aria-label="Foto: Geschäftsgespräch am Tisch mit Handschlag zwischen Bewerberin und zwei Personalverantwortlichen"></div>
</section>

<!-- Page: 6 Schritte -->
<section class="page p3">
  <h1 class="page-title">In 6 Schritten zu Ihrer neuen Fachkraft</h1>
  <svg class="art" width="406" height="572" viewBox="0 0 406 572">
    <line x1="204" y1="108" x2="204" y2="436" stroke="#cfd3d3" stroke-width="6"/>
    <g stroke-width="7">
      <line x1="154" y1="108" x2="317" y2="108" stroke="var(--ink)"/>
      <line x1="92" y1="174" x2="255" y2="174" stroke="var(--ink)"/>
      <line x1="154" y1="238" x2="317" y2="238" stroke="var(--ink)"/>
      <line x1="92" y1="302" x2="255" y2="302" stroke="var(--green)"/>
      <line x1="154" y1="367" x2="317" y2="367" stroke="var(--mint-soft)"/>
      <line x1="92" y1="436" x2="255" y2="436" stroke="var(--green)"/>
    </g>
    <g>
      <circle cx="154" cy="108" r="10" fill="var(--ink)"/>
      <circle cx="255" cy="174" r="10" fill="var(--green)"/>
      <circle cx="154" cy="238" r="10" fill="var(--mint-soft)"/>
      <circle cx="255" cy="302" r="10" fill="var(--ink)"/>
      <circle cx="154" cy="367" r="10" fill="var(--green)"/>
      <circle cx="255" cy="436" r="10" fill="var(--ink)"/>
    </g>
    <g fill="#fff" stroke-width="3.5">
      <circle cx="317" cy="108" r="15" stroke="var(--ink)"/>
      <circle cx="92" cy="174" r="15" stroke="var(--green)"/>
      <circle cx="317" cy="238" r="15" stroke="var(--mint-soft)"/>
      <circle cx="92" cy="302" r="15" stroke="var(--ink)"/>
      <circle cx="317" cy="367" r="15" stroke="var(--green)"/>
      <circle cx="92" cy="436" r="15" stroke="var(--ink)"/>
    </g>
    <g font-family="Heebo, Arial, sans-serif" font-weight="700" font-size="12" fill="var(--ink)" text-anchor="middle">
      <text x="317" y="112">1</text><text x="92" y="178">2</text><text x="317" y="242">3</text>
      <text x="92" y="306">4</text><text x="317" y="371">5</text><text x="92" y="440">6</text>
    </g>
    <g fill="#fff" stroke-width="5">
      <circle cx="204" cy="108" r="26" stroke="var(--ink)"/>
      <circle cx="204" cy="174" r="26" stroke="var(--green)"/>
      <circle cx="204" cy="238" r="26" stroke="var(--mint-soft)"/>
      <circle cx="204" cy="302" r="26" stroke="var(--ink)"/>
      <circle cx="204" cy="367" r="26" stroke="var(--green)"/>
      <circle cx="204" cy="436" r="26" stroke="var(--ink)"/>
    </g>
    <g fill="none" stroke="var(--ink)" stroke-width="1.5" stroke-linecap="round" stroke-linejoin="round">
      <rect x="194" y="96" width="20" height="24" rx="2"/><circle cx="204" cy="105" r="3"/><path d="M198 115c1-4 11-4 12 0"/>
      <rect x="194" y="162" width="18" height="24" rx="2" fill="var(--ink)"/><path d="M198 168h9M198 173h9M198 178h6" stroke="#fff"/><path d="M208 182l8-8"/>
      <circle cx="197" cy="240" r="3"/><circle cx="204" cy="236" r="3"/><circle cx="211" cy="240" r="3"/><path d="M191 250c0-5 12-5 12 0M198 250c0-6 12-6 12 0M205 250c0-5 12-5 12 0M200 228l3 3 5-5"/>
      <path d="M193 305h22M196 305v9M212 305v9"/><circle cx="197" cy="296" r="2.5"/><circle cx="211" cy="296" r="2.5"/><rect x="200" y="288" width="8" height="6" rx="1"/>
      <circle cx="204" cy="365" r="3"/><path d="M199 375c0-5 10-5 10 0M193 356h5M210 356h5M193 378h5M210 378h5"/>
      <path d="M190 436l7-7h6l4 4 5-4 6 7-9 8-6-5"/>
    </g>
  </svg>

  <div class="tl-text" style="left:16px;top:92px;width:120px"><h3>Kontaktaufnahme</h3>Sie nehmen Kontakt zu uns auf und teilen uns Ihren Personalbedarf, sowie spezielle Stellenanforderungen mit.</div>
  <div class="tl-text right" style="left:274px;top:160px;width:106px"><h3>Vertragsmodalitäten</h3>Wir setzen uns mit Ihnen zusammen, besprechen die Einzelheiten und klären die Rahmenbedingungen, individuell auf Sie zugeschnitten.</div>
  <div class="tl-text" style="left:16px;top:220px;width:120px"><h3>Kandidatenvorauswahl</h3>Wir lassen Ihnen vorab übersichtliche CV's potenzieller Kandidat:innen zukommen und Sie treffen eine Vorauswahl bzw. teilen uns eventuelle Anpassungswünsche mit.</div>
  <div class="tl-text right" style="left:274px;top:288px;width:106px"><h3>Vorstellungsgespräche</h3>Sie führen die Vorstellungsgespräche mit den Kandidat:innen durch. Unsere Expert:innen begleiten Sie dabei als wichtiges Bindeglied, um bei Missverständnissen und Unklarheiten vorzubeugen.</div>
  <div class="tl-text right" style="left:16px;top:355px;width:120px"><h3>Finale Personalauswahl</h3>Sie entscheiden sich für Ihre Wunschmitarbeiter:innen - wir stellen Ihnen zusammen mit einer persönlichen Einschätzung zu den jeweiligen Kandidat:innen alle Informationen und Unterlagen in einem übersichtlichen und informativen Bericht zur Verfügung.</div>
  <div class="tl-text right" style="left:274px;top:423px;width:106px"><h3>Arbeitsvertrag</h3>Nach Klärung aller wichtigen Modalitäten und Besonderheiten unterschreibt der/die Bewerber:in seinen/ihren Arbeitsvertrag.</div>

  <div class="first-day">
    <h2>Erster Arbeitstag</h2>
    <p>Wir begleiten und betreuen unsere Kandidat:innen über den kompletten Auswahlprozess hinweg bis zum Ende ihrer Probezeit. Nicht selten können wir auch nach der erfolgreichen Vermittlung noch wertvolle Klärungs- und Motivationsarbeit leisten. Außerdem übernehmen wir sowohl Abschlussgespräche, als auch die gesamte Korrespondenz mit allen Bewerber:innen, die am Auswahlverfahren beteiligt waren.</p>
  </div>
  <footer class="footer"><span>+49 000 555 01 230</span><span>hr@veldara-hr.example</span><span>www.veldara-hr.example</span></footer>
</section>

<!-- Page: Talentpool -->
<section class="page p4">
  <div class="photo-team" role="img" aria-label="Foto: Gruppe medizinischer Fachkräfte in Kitteln und Kasacks in einer hellen Klinik"></div>
  <h1 class="page-title">Unser Talentpool</h1>
  <p class="talent-list">Gesundheits- und Krankenpfleger:in I Pflegefachmann /-frau I Pflegefachassistent:in I Altenpfleger:in I Arzt/Ärztin I Hebamme I Anästhesietechnische:r Assistent:in (ATA) I Operationstechnische:r Assistent:in (OTA) I Medizinisch-technische:r Laborassistent:in (MTLA) I Medizinisch-technische:r Radiologieassistentin (MTRA) I Pflegehilfskräfte I Pflegefachassistent:in I Notfallsanitäter:in I Rettungssanitäter:in I Physiotherapeut:innen I</p>
  <p class="talent-more">… und viele weitere medizinische Berufe.</p>
  <div class="photo-hands" role="img" aria-label="Foto: Handschlag über einem Schreibtisch mit Unterlagen"></div>
  <footer class="footer"><span>+49 000 555 01 230</span><span>hr@veldara-hr.example</span><span>www.veldara-hr.example</span></footer>
</section>

</body>
</html>
```